Business Card Design

We are looking for a business card designed for our landscaping company. We do landscaping installation & Maintenance Services. We would like to see designs that have basic landscaping in background. We also think it is important to have both of our names and phone numbers on the card. We need something that stands out a little whether it is shape of the card or thickness or design.

Business

Bramblewood Yardworks, bramblewoodyard@mailvista.net, Owen Platt 555-273-9104, Daniel Korbin 555-618-3927

```html
<!DOCTYPE html>
<html lang="en">
<head>
<meta charset="utf-8">
<title>Bramblewood Yardworks — Business Card</title>
<link rel="stylesheet" href="https://fonts.googleapis.com/css2?family=Noto+Sans:wght@400;600&display=swap">
<style>
  :root {
    --page-bg: #e9e6e1;
    --card-white: #f7f7f7;
    --card-slate: #4b4f57;
    --card-slate-dark: #3f434a;
    --accent-red: #d8203a;
    --ink-dark: #111111;
    --ink-light: #f1f2f4;
  }
  html, body {
    margin: 0;
    width: 1200px;
    height: 892px;
    overflow: hidden;
    background: var(--page-bg);
  }
  .canvas {
    position: relative;
    width: 1200px;
    height: 892px;
  }
  .business-card {
    position: absolute;
    left: 100px;
    top: 160px;
    width: 1000px;
    height: 572px;
    background: var(--card-white);
    box-shadow: 0 10px 30px rgba(0,0,0,0.18);
    overflow: hidden;
    font-family: "Noto Sans", sans-serif;
  }
  .card-shapes {
    position: absolute;
    inset: 0;
  }
  .company-name {
    position: absolute;
    left: 150px;
    top: 88px;
    margin: 0;
    font-size: 48px;
    font-weight: 600;
    letter-spacing: 4px;
    color: var(--ink-dark);
  }
  .contact {
    position: absolute;
    color: var(--ink-light);
    letter-spacing: 3px;
  }
  .contact-name {
    margin: 0 0 8px;
    font-size: 29px;
    font-weight: 400;
  }
  .contact-phone {
    margin: 0;
    font-size: 31px;
    display: flex;
    align-items: center;
    gap: 14px;
  }
  .phone-icon {
    width: 22px;
    height: 22px;
    flex: none;
  }
  .contact--first { left: 138px; top: 342px; }
  .contact--second { left: 620px; top: 360px; }
  .card-email {
    position: absolute;
    left: 240px;
    top: 478px;
    margin: 0;
    font-size: 27px;
    letter-spacing: 3px;
    color: var(--ink-light);
  }
</style>
</head>
<body>
<main class="canvas">
  <article class="business-card">
    <svg class="card-shapes" width="1000" height="572" viewBox="0 0 1000 572" aria-hidden="true">
      <defs>
        <linearGradient id="slateGradient" x1="0" y1="0" x2="1" y2="1">
          <stop offset="0" stop-color="var(--card-slate)"/>
          <stop offset="1" stop-color="var(--card-slate-dark)"/>
        </linearGradient>
      </defs>
      <polygon points="0,232 120,292 860,292 1000,250 1000,572 0,572" fill="url(#slateGradient)"/>
      <polygon points="110,238 860,264 1000,220 1000,234 862,278 120,254" fill="var(--accent-red)"/>
    </svg>

    <h1 class="company-name">Bramblewood Yardworks</h1>

    <section class="contact contact--first">
      <p class="contact-name">Owen Platt</p>
      <p class="contact-phone">
        <svg class="phone-icon" viewBox="0 0 22 22" aria-hidden="true">
          <rect width="22" height="22" rx="2" fill="var(--ink-light)"/>
          <path d="M7 4 L10 5 L9.5 8.5 L8 9.5 Q9.5 13 12.5 14 L13.5 12.5 L17 13 L18 16 Q15 19 11 16.5 Q6 13 5 8 Q5 5 7 4 Z" fill="var(--card-slate)"/>
        </svg>
        555-273-9104
      </p>
    </section>

    <section class="contact contact--second">
      <p class="contact-name">Daniel Korbin</p>
      <p class="contact-phone">
        <svg class="phone-icon" viewBox="0 0 22 22" aria-hidden="true">
          <rect width="22" height="22" rx="2" fill="var(--ink-light)"/>
          <path d="M7 4 L10 5 L9.5 8.5 L8 9.5 Q9.5 13 12.5 14 L13.5 12.5 L17 13 L18 16 Q15 19 11 16.5 Q6 13 5 8 Q5 5 7 4 Z" fill="var(--card-slate)"/>
        </svg>
        555-618-3927
      </p>
    </section>

    <p class="card-email">bramblewoodyard@mailvista.net</p>
  </article>
</main>
</body>
</html>
```